Varnik Holdings — Business Card Design Brief
Overview
Design a double-sided business card for Varnik Holdings that highlights our two service arms: Varnik Communications (telecommunications) and Varnik Energy (business energy solutions). The card should feel smart and stand out when handed to clients.

Objectives
Showcase our areas of specialty clearly.
Reflect the overall Varnik / Varnik Holdings brand while acknowledging both arms.
Explore using both logos (Communications + Energy) or one unified logo, depending on the design.

Deliverables
One double-sided business card design (front + back).

Content & Copy
Front (preferred): Logo: Varnik / Varnik Holdings
Descriptor: Business Communications | Business Energy
Back:My contact details and company details
Core products: Business Mobile • Telephony • Internet • Business Energy Solutions

Brand & Visual Direction
We have a group logo currently tailored more toward telecoms, plus a separate Varnik Energy logo.
Please explore layouts that use both logos or just one, whichever works best.
Color: I wouldn't mind seeing an option using our the Blue/Purple gradient from our website (varnik-example.co.uk), but also open to non-gradient approaches and other colours..

Overall look: Smart, modern, and distinctive.
Format & Print Specs
Double-sided business card format. (Use a standard size

Must-Haves
Front: Varnik wording or Varnik Holdings wording with atleast 1 logo also on front “Business Communications | Business Energy.”

Back: Contact + company details and core products.
A design that stands out while remaining professional.

Nice-to-Have Options
A gradient version using our site’s Blue/Purple gradient.
A non-gradient version.
A dual-logo treatment versus a single-logo treatment.

Thanks
Owen

```html
<!DOCTYPE html>
<html lang="en">
<head>
<meta charset="utf-8">
<title>Varnik Holdings — Business Card</title>
<link rel="stylesheet" href="https://fonts.googleapis.com/css2?family=Montserrat:wght@400;500;600;700&family=Poppins:wght@600;700&family=Tinos&display=swap">
<style>
  :root {
    --stage: #9a9a9a;
    --card: #ffffff;
    --navy: #1c1464;
    --green: #45ad0c;
    --blue: #1f6fd6;
    --ink: #1e1e1e;
    --charcoal: #323232;
    --rule: #333333;
  }
  * { margin: 0; padding: 0; box-sizing: border-box; }
  html, body { width: 1200px; height: 1059px; overflow: hidden; }
  body { background: var(--stage); position: relative; font-family: "Montserrat", sans-serif; }

  .card {
    position: absolute;
    background: var(--card);
    border-radius: 26px;
    overflow: hidden;
    box-shadow: 0 14px 26px rgba(0,0,0,0.35);
  }
  .card--front { left: 252px; top: 88px; width: 724px; height: 415px; }
  .card--back  { left: 252px; top: 567px; width: 712px; height: 406px; }

  /* brand lockup */
  .brand { position: absolute; display: flex; flex-direction: column; align-items: center; }
  .brand__dot { border-radius: 50%; }
  .brand__name { font-family: "Montserrat", sans-serif; font-weight: 700; color: var(--navy); letter-spacing: 1px; line-height: 1; }

  .card--front .brand { left: 456px; top: 30px; width: 200px; }
  .card--front .brand__dot { width: 92px; height: 92px; background: var(--green); }
  .card--front .brand__name { font-size: 40px; margin-top: 10px; }

  .descriptor {
    position: absolute; right: 50px; top: 196px;
    font-weight: 600; font-size: 13px; color: var(--green);
    letter-spacing: 0.2px; white-space: nowrap;
  }

  .holder { position: absolute; left: 41px; top: 158px; }
  .holder__name { font-weight: 700; font-size: 29px; color: var(--navy); }
  .holder__role { font-family: "Tinos", serif; font-size: 18px; color: var(--ink); margin-top: 6px; }

  .divider { position: absolute; left: 41px; right: 50px; top: 236px; height: 1.5px; background: var(--rule); }

  .contacts { position: absolute; left: 37px; top: 252px; list-style: none; }
  .contacts li { display: flex; align-items: center; height: 33.5px; font-size: 19.5px; color: var(--ink); white-space: nowrap; }
  .contacts svg { width: 22px; height: 22px; margin-right: 10px; flex: none; }
  .contacts li.address { margin-top: 3px; }

  .services { position: absolute; right: 50px; top: 255px; text-align: right; list-style: none; }
  .services li { font-weight: 700; font-size: 19px; color: var(--navy); line-height: 28px; white-space: nowrap; }

  .band { position: absolute; left: 0; right: 0; bottom: 0; height: 12px; }

  /* back */
  .group-title { position: absolute; left: 0; right: 0; top: 72px; text-align: center; font-family: "Poppins", sans-serif; font-weight: 700; font-size: 50px; color: var(--charcoal); }
  .card--back .brand { left: 0; right: 0; top: 158px; }
  .card--back .brand__dot { width: 118px; height: 118px; background: var(--blue); }
  .card--back .brand__name { font-size: 50px; margin-top: 16px; }
</style>
</head>
<body>

<section class="card card--front" aria-label="Card front">
  <div class="brand">
    <span class="brand__dot"></span>
    <span class="brand__name">VARNIK</span>
  </div>
  <p class="descriptor">Business Communications | Business Energy</p>

  <div class="holder">
    <h1 class="holder__name">Marcus Hale</h1>
    <p class="holder__role">Owner</p>
  </div>

  <div class="divider"></div>

  <ul class="contacts">
    <li>
      <svg viewBox="0 0 24 24" aria-hidden="true"><path fill="#45ad0c" d="M6.6 10.8a15.2 15.2 0 0 0 6.6 6.6l2.2-2.2c.3-.3.7-.4 1-.2 1.1.4 2.3.6 3.6.6.6 0 1 .4 1 1V20c0 .6-.4 1-1 1A17 17 0 0 1 3 4c0-.6.4-1 1-1h3.5c.6 0 1 .4 1 1 0 1.3.2 2.5.6 3.6.1.3 0 .7-.2 1z"/></svg>
      044-000 555 210
    </li>
    <li>
      <svg viewBox="0 0 24 24" aria-hidden="true"><rect x="2" y="5" width="20" height="14" fill="#45ad0c"/><path d="M2 5l10 8 10-8" fill="none" stroke="#fff" stroke-width="1.8"/></svg>
      info@varnik-example.co.uk
    </li>
    <li>
      <svg viewBox="0 0 24 24" aria-hidden="true"><circle cx="12" cy="12" r="10" fill="#45ad0c"/><path d="M2 12h20M12 2c3 3 3 17 0 20M12 2c-3 3-3 17 0 20" fill="none" stroke="#fff" stroke-width="1.4"/></svg>
      www.varnik-example.co.uk
    </li>
    <li class="address">
      <svg viewBox="0 0 24 24" aria-hidden="true"><path fill="#45ad0c" d="M12 1a8 8 0 0 0-8 8c0 6 8 14 8 14s8-8 8-14a8 8 0 0 0-8-8z"/><circle cx="12" cy="9" r="3" fill="#fff"/></svg>
      17 Harrow Lane, Brightfield BF4 2QL, United Kingdom
    </li>
  </ul>

  <ul class="services">
    <li>• Business Mobile</li>
    <li>• Telephony • Internet</li>
    <li>• Business Energy Solutions</li>
  </ul>

  <svg class="band" viewBox="0 0 724 12" preserveAspectRatio="none" aria-hidden="true">
    <polygon points="0,0 357,0 362,12 0,12" fill="#1c1464"/>
    <polygon points="360,0 724,0 724,12 365,12" fill="#45ad0c"/>
  </svg>
</section>

<section class="card card--back" aria-label="Card back">
  <h2 class="group-title">Varnik Holdings</h2>
  <div class="brand">
    <span class="brand__dot"></span>
    <span class="brand__name">VARNIK</span>
  </div>
</section>

</body>
</html>
```